Business Card Design

IT Solutions company.

I need a professional looking design with my company logo if possible.

Logo is located here:
http://www.brunelwavesystems.co.uk/dev/images/logo1.jpg
Feel free to redesign the logo if you think you have any better suggestions.

Our services include, IT Infrastructure/Telephony Maintenance & Hosting Services. Linux and Windows Solutions, App Development.

Out website is currently under development:
http://www.brunelwavesystems.co.uk/dev/

I'm looking for a colourful but professional looking business card.

Industry/Entity Type

Business

Contact Information for Business Card

BW Brunel Wavesystems Ltd
Martin Hollisby
07700958312
www.brunelwavesystems.co.uk
mhollisby@brunelwavesystems.co.uk

```html
<!DOCTYPE html>
<html lang="en">
<head>
<meta charset="utf-8">
<title>Brunel Wavesystems Ltd – Business Card</title>
<link rel="stylesheet" href="https://fonts.googleapis.com/css2?family=Bitter:wght@400;500&family=Arimo:wght@700&display=swap">
<style>
  :root {
    --stage: #e9e7e4;
    --card-white: #ffffff;
    --brand-blue: #1f3ff0;
    --ink-dark: #2c2e30;
    --card-dark: #2a2c2d;
    --text-light: #ffffff;
    --text-soft: #e4e4e4;
  }
  * { box-sizing: border-box; margin: 0; padding: 0; }
  html, body {
    width: 1200px; height: 483px; overflow: hidden;
    background: var(--stage);
  }
  .stage {
    position: relative; width: 1200px; height: 483px;
    display: flex; align-items: center; justify-content: center; gap: 60px;
  }
  .card {
    position: relative; width: 540px; height: 310px; overflow: hidden;
    box-shadow: 0 4px 14px rgba(0,0,0,0.18);
  }

  /* Front */
  .card-front { background: var(--card-white); font-family: "Bitter", serif; }
  .front-swoosh { position: absolute; inset: 0; width: 540px; height: 310px; }
  .holder-name {
    position: absolute; top: 26px; right: 28px;
    color: var(--text-light); font-size: 21px; font-weight: 400; letter-spacing: 0.3px;
  }
  .brand-name {
    position: absolute; top: 134px; left: 44px;
    color: var(--ink-dark); font-size: 25px; font-weight: 500; line-height: 1.1;
  }
  .contact-list {
    position: absolute; left: 50px; bottom: 24px; list-style: none;
    color: var(--ink-dark); font-size: 16px;
  }
  .contact-list li { display: flex; align-items: center; gap: 8px; margin-top: 8px; }
  .contact-icon { width: 13px; height: 13px; flex: none; fill: var(--ink-dark); }

  /* Back */
  .card-back {
    background: var(--card-dark); color: var(--text-soft);
    font-family: "Arimo", Arial, sans-serif; font-weight: 700; text-align: center;
  }
  .services { position: relative; padding-top: 56px; }
  .services-title { font-size: 14px; color: var(--text-light); }
  .services-rule {
    width: 200px; height: 1px; margin: 7px auto 10px;
    background: linear-gradient(90deg, transparent, var(--text-light), transparent);
  }
  .services-list { list-style: none; font-size: 14px; line-height: 1.5; }
  .services-list li::before { content: "• "; }
  .services-site { margin-top: 34px; font-size: 13px; letter-spacing: 0.4px; color: var(--text-light); }
</style>
</head>
<body>
<main class="stage">
  <section class="card card-front" aria-label="Business card front">
    <svg class="front-swoosh" viewBox="0 0 540 310" aria-hidden="true">
      <path d="M0 0 H540 V214 C505 120 340 70 0 80 Z" fill="var(--brand-blue)"/>
      <path d="M0 88 C340 78 505 128 540 226 V262 C500 142 340 96 0 95 Z" fill="var(--ink-dark)"/>
    </svg>
    <h1 class="holder-name">Martin Hollisby</h1>
    <p class="brand-name">Brunel Wavesystems Ltd</p>
    <ul class="contact-list">
      <li>
        <svg class="contact-icon" viewBox="0 0 16 16" aria-hidden="true"><path d="M3.5 1 6 3.5 4.6 5.6c.9 2.3 3.5 4.9 5.8 5.8L12.5 10 15 12.5 13 15C6.5 14.6 1.4 9.5 1 3Z"/></svg>
        <span>07700958312</span>
      </li>
      <li>
        <svg class="contact-icon" viewBox="0 0 16 16" aria-hidden="true"><path d="M1 4h14v9H1Zm1.5 1.2L8 9l5.5-3.8V5h-11Z"/></svg>
        <span>mhollisby@brunelwavesystems.co.uk</span>
      </li>
      <li>
        <svg class="contact-icon" viewBox="0 0 16 16" aria-hidden="true"><circle cx="8" cy="8" r="7"/><path d="M1 8h14M8 1c-3 3.5-3 10.5 0 14M8 1c3 3.5 3 10.5 0 14" stroke="#fff" stroke-width="1" fill="none"/></svg>
        <span>www.brunelwavesystems.co.uk</span>
      </li>
    </ul>
  </section>

  <section class="card card-back" aria-label="Business card back">
    <div class="services">
      <h2 class="services-title">Our Services Include</h2>
      <div class="services-rule"></div>
      <ul class="services-list">
        <li>IT Infrastructure/Telephony Maintenance</li>
        <li>Hosting Services</li>
        <li>Linux and Windows Solutions</li>
        <li>App Development</li>
      </ul>
      <p class="services-site">www.brunelwavesystems.co.uk</p>
    </div>
  </section>
</main>
</body>
</html>
```